RWT Fittings Ltd Business Cards

We need a business card with our business logo. We provide window and door installations on high-rises in west coast British Colombia, Canada.

I would like my business information and details on one side of the card, and the other side the company name with logo

Target Market(s)

General Contractors

Industry/Entity Type

Construction

Contact Information for Business Card

one side i want my company name and logo in the dark theme logo that i provided

Requirements
Must have
• Marco Peltieri, 16045518293, RWTFittings@mailbox-demo.com, 1407-5194 Linden Row Burnaby BC, V5H 2K9, Owner & Manager

```html
<!DOCTYPE html>
<html lang="en">
<head>
<meta charset="utf-8">
<title>RWT Fittings Ltd Business Cards</title>
<link rel="stylesheet" href="https://fonts.googleapis.com/css2?family=Open+Sans:wght@400;700&display=swap">
<style>
  :root {
    --backdrop: #4a4a4a;
    --card-black: #191919;
    --band-grey: #9b9b9b;
    --brand-blue: #29abe2;
    --text-white: #f2f2f2;
    --emboss-grey: #2c2c2c;
  }
  * { margin: 0; padding: 0; box-sizing: border-box; }
  html, body { width: 1200px; height: 801px; overflow: hidden; }
  body {
    background: var(--backdrop);
    font-family: "Open Sans", Arial, sans-serif;
    display: flex;
    align-items: center;
    justify-content: center;
    gap: 40px;
  }
  .card {
    position: relative;
    width: 540px;
    height: 309px;
    background: var(--card-black);
    overflow: hidden;
    box-shadow: 0 14px 30px rgba(0,0,0,.45);
  }
  .footer-band {
    position: absolute;
    left: 0;
    right: 0;
    bottom: 0;
    height: 64px;
    background: linear-gradient(90deg, #8e8e8e, var(--band-grey));
  }
  .brand {
    position: absolute;
    display: flex;
    align-items: center;
    gap: 10px;
    font-weight: 700;
    letter-spacing: .04em;
    white-space: nowrap;
  }
  .card-front .brand {
    left: 28px;
    top: 108px;
    font-size: 20px;
    color: var(--brand-blue);
  }
  .brand-square {
    display: inline-block;
    background: currentColor;
  }
  .card-front .brand-square { width: 18px; height: 18px; }
  .divider {
    position: absolute;
    left: 256px;
    top: 36px;
    width: 1px;
    height: 150px;
    background: var(--brand-blue);
  }
  .contact {
    position: absolute;
    left: 274px;
    top: 28px;
    color: var(--text-white);
    font-size: 11.5px;
    line-height: 18px;
  }
  .contact-name {
    color: var(--brand-blue);
    font-size: 17px;
    font-weight: 700;
    line-height: 22px;
    text-transform: uppercase;
  }
  .contact-title { font-size: 12px; margin-bottom: 8px; }
  .contact-line { display: flex; align-items: center; gap: 6px; }
  .contact-line svg { width: 11px; height: 11px; flex: none; fill: var(--brand-blue); }
  .contact-address { margin-top: 8px; line-height: 16px; }
  .card-back .brand {
    left: 50%;
    top: 50%;
    transform: translate(-50%, -50%);
    font-size: 36px;
    color: var(--emboss-grey);
  }
  .card-back .brand-square { width: 32px; height: 32px; }
</style>
</head>
<body>
  <section class="card card-front" aria-label="Business card front">
    <div class="footer-band" role="img" aria-label="Grey decorative band with blue accent"></div>
    <div class="brand"><span class="brand-square"></span>RWT FITTINGS LTD</div>
    <div class="divider"></div>
    <div class="contact">
      <p class="contact-name">Marco Peltieri</p>
      <p class="contact-title">Owner &amp; Manager</p>
      <p class="contact-line">
        <svg viewBox="0 0 12 12"><path d="M2.5 0.5 L4.5 2.8 L3.4 4.3 C4.2 5.9 5.9 7.6 7.6 8.5 L9.1 7.4 L11.5 9.4 L10 11.5 C5 11 1 7 0.5 2 Z"/></svg>
        16045518293
      </p>
      <p class="contact-line">
        <svg viewBox="0 0 12 12"><path d="M0.5 2 H11.5 V10 H0.5 Z M1.2 2.6 L6 6.4 L10.8 2.6" stroke="var(--card-black)" stroke-width=".8"/></svg>
        RWTFittings@mailbox-demo.com
      </p>
      <p class="contact-line">
        <svg viewBox="0 0 12 12"><circle cx="6" cy="6" r="5.5"/><path d="M0.5 6 H11.5 M6 0.5 C3.5 3 3.5 9 6 11.5 M6 0.5 C8.5 3 8.5 9 6 11.5" fill="none" stroke="var(--card-black)" stroke-width=".7"/></svg>
        www.rwtfittings-demo.com
      </p>
      <p class="contact-address">1407-5194 Linden Row<br>Burnaby BC, V5H 2K9</p>
    </div>
  </section>

  <section class="card card-back" aria-label="Business card back">
    <div class="brand"><span class="brand-square"></span>RWT FITTINGS LTD</div>
  </section>
</body>
</html>
```